Veltrane Group Business Card Design

The CEO is looking for a new trendy look for his business card.
You can stay with current branding or come up with something new/creative. It can be 3D, including Medical Office buildings. You can use our logo in a variety of colors. Please include name, title, company name, company website, email address, cell number

Target Market(s)

Real Estate Development and Construction

Industry/Entity Type

Health care real estate

Contact Information for Business Card

Rohesh Kamdar, CEO M-604.781.2249 E-roheshkamdar@veltrane.com Address:4180 Lindqvist Ave, Tampa, FL 33482 www.veltrane.com

Font styles to use
Other font styles liked:
• Be creative

Requirements
Must have
• Creative, trendy look
Nice to have
• Please go to our website to get a feel- www. veltrane.com
Should not have
• small fonts

```html
<!DOCTYPE html>
<html lang="en">
<head>
<meta charset="utf-8">
<title>Veltrane Group Business Card</title>
<link rel="stylesheet" href="https://fonts.googleapis.com/css2?family=Archivo:wght@400;800&display=swap">
<style>
  :root {
    --bg: #3e3e3e;
    --red: #b01f2b;
    --navy: #1f3156;
    --white: #ffffff;
    --ink: #3a3a3a;
  }
  html, body {
    margin: 0;
    padding: 0;
    width: 1200px;
    height: 803px;
    overflow: hidden;
    background: var(--bg);
    font-family: "Archivo", Arial, sans-serif;
  }
  .stage {
    position: relative;
    width: 1200px;
    height: 803px;
  }
  .card {
    position: absolute;
    top: 247px;
    width: 540px;
    height: 309px;
    border-radius: 22px;
    overflow: hidden;
    box-shadow: 0 14px 30px rgba(0,0,0,0.35);
  }
  .card--front { left: 40px; background: var(--white); }
  .card--back { left: 620px; background: var(--red); }

  .front-art {
    position: absolute;
    inset: 0;
    width: 540px;
    height: 309px;
  }
  .brand {
    position: absolute;
    margin: 0;
    font-weight: 800;
    line-height: 1;
    letter-spacing: -1px;
  }
  .card--front .brand {
    left: 34px;
    top: 92px;
    font-size: 46px;
    color: var(--red);
  }
  .contact {
    position: absolute;
    left: 36px;
    top: 160px;
    color: var(--ink);
    font-size: 13px;
    line-height: 1.35;
  }
  .contact__name {
    margin: 0;
    font-size: 21px;
    font-weight: 800;
    color: var(--red);
  }
  .contact__title {
    margin: 0 0 8px;
    font-size: 14px;
    color: var(--navy);
  }
  .contact__address { margin: 0 0 8px; }
  .contact__list { list-style: none; margin: 0; padding: 0; }
  .contact__item { display: flex; align-items: center; gap: 7px; }
  .contact__icon { width: 11px; height: 11px; fill: var(--red); flex: none; }

  .card--back .brand {
    left: 0;
    right: 0;
    top: 100px;
    text-align: center;
    font-size: 66px;
    color: var(--white);
  }
  .back-web {
    position: absolute;
    left: 0;
    right: 0;
    bottom: 34px;
    margin: 0;
    text-align: center;
    color: var(--white);
    font-size: 15px;
  }
</style>
</head>
<body>
<main class="stage">
  <section class="card card--front" aria-label="Business card front">
    <svg class="front-art" viewBox="0 0 540 309" aria-hidden="true">
      <rect x="300" y="0" width="240" height="309" fill="var(--red)"/>
      <path d="M430 0 H540 V70 Q500 20 430 0 Z" fill="var(--navy)"/>
      <circle cx="250" cy="210" r="255" fill="var(--white)"/>
    </svg>
    <p class="brand">Veltrane Group</p>
    <div class="contact">
      <p class="contact__name">Rohesh Kamdar</p>
      <p class="contact__title">CEO</p>
      <p class="contact__address">4180 Lindqvist Ave, Tampa<br>FL 33482</p>
      <ul class="contact__list">
        <li class="contact__item">
          <svg class="contact__icon" viewBox="0 0 12 12"><path d="M2 1 L4.5 1 L5.3 3.6 L3.9 4.6 Q5 7 7.4 8.1 L8.4 6.7 L11 7.5 L11 10 Q10 11 8.5 11 Q1 9 1 3.5 Q1 2 2 1 Z"/></svg>
          604.781.2249
        </li>
        <li class="contact__item">
          <svg class="contact__icon" viewBox="0 0 12 12"><path d="M0 2 H12 V10 H0 Z M0.8 2.6 L6 6.6 L11.2 2.6" stroke="var(--white)" stroke-width="0.9"/></svg>
          roheshkamdar@veltrane.com
        </li>
        <li class="contact__item">
          <svg class="contact__icon" viewBox="0 0 12 12"><circle cx="6" cy="6" r="5.5"/><path d="M0.5 6 H11.5 M6 0.5 Q3 6 6 11.5 M6 0.5 Q9 6 6 11.5" stroke="var(--white)" stroke-width="0.8" fill="none"/></svg>
          www.veltrane.com
        </li>
      </ul>
    </div>
  </section>

  <section class="card card--back" aria-label="Business card back">
    <p class="brand">Veltrane Group</p>
    <p class="back-web">www.veltrane.com</p>
  </section>
</main>
</body>
</html>
```